Brindovalle Business cards

Dear team, I need to get the design file to suit it to our team. The focus of the business card is the Automotive Market and the design must be in black colour and the logo must be in glossy black. On the front of the card I need to get the following info:

- Name and Surname
- Title
- eMail
- Phone Number
- Skype account
- domain address

```html
<!DOCTYPE html>
<html lang="en">
<head>
<meta charset="utf-8">
<title>Brindovalle Business Cards</title>
<link href="https://fonts.googleapis.com/css2?family=Archivo:wght@400;500;800&display=swap" rel="stylesheet">
<style>
  :root {
    --red: #ec2f38;
    --navy: #0a0f35;
    --white: #ffffff;
    --ink: #1a1a1a;
    --backdrop: #e6e7ea;
  }
  * { margin: 0; padding: 0; box-sizing: border-box; }
  html, body { width: 1200px; height: 900px; overflow: hidden; }
  body {
    background: var(--backdrop);
    font-family: "Archivo", Arial, sans-serif;
    position: relative;
  }
  .card {
    position: absolute;
    left: 270px;
    width: 660px;
    height: 377px;
    border-radius: 18px;
    overflow: hidden;
    box-shadow: 0 10px 28px rgba(0,0,0,0.18);
  }
  .card--front { top: 50px; background: var(--white); }
  .card--back { top: 473px; background: var(--navy); }

  .front-graphic { position: absolute; inset: 0; }

  .contact {
    position: absolute;
    right: 36px;
    top: 66px;
    text-align: right;
    color: var(--ink);
  }
  .contact__name {
    color: var(--red);
    font-weight: 800;
    font-size: 25px;
    letter-spacing: 0.5px;
    text-transform: uppercase;
    white-space: nowrap;
  }
  .contact__title { font-size: 16px; margin-top: 2px; margin-bottom: 14px; }
  .contact__line {
    font-size: 16px;
    line-height: 22px;
    display: flex;
    justify-content: flex-end;
    align-items: center;
    gap: 7px;
    white-space: nowrap;
  }
  .contact__icon { width: 13px; height: 13px; flex: none; }

  .wordmark {
    position: absolute;
    font-weight: 800;
    letter-spacing: -0.5px;
    white-space: nowrap;
  }
  .wordmark--front {
    color: var(--red);
    font-size: 40px;
    left: 256px;
    bottom: 28px;
  }
  .back-lockup {
    position: absolute;
    left: 50%;
    top: 50%;
    transform: translate(-50%, -50%);
    display: flex;
    align-items: center;
    gap: 18px;
  }
  .back-lockup__dot {
    width: 34px; height: 34px;
    border-radius: 50%;
    background: var(--red);
  }
  .wordmark--back {
    position: static;
    color: var(--white);
    font-size: 56px;
  }
</style>
</head>
<body>

<section class="card card--front" aria-label="Business card front">
  <svg class="front-graphic" viewBox="0 0 660 377" width="660" height="377" aria-hidden="true">
    <polygon points="0,0 380,0 200,377 0,377" fill="var(--red)"/>
    <path d="M0,42 L120,42 C215,42 262,120 254,200 C246,268 200,318 120,336 L0,350 Z" fill="var(--white)"/>
  </svg>

  <div class="contact">
    <p class="contact__name">Marlo Kessner</p>
    <p class="contact__title">Director</p>
    <p class="contact__line">2284 W Calder Ave, Fenwick,</p>
    <p class="contact__line">Oregon 97021</p>
    <p class="contact__line">555-204-7318
      <svg class="contact__icon" viewBox="0 0 16 16"><path d="M4 1 L6.5 4.5 L5 6.5 C6 8.5 7.5 10 9.5 11 L11.5 9.5 L15 12 L13 15 C7 15 1 9 1 3 Z" fill="var(--red)"/></svg>
    </p>
    <p class="contact__line">info@brindovalle.com
      <svg class="contact__icon" viewBox="0 0 16 16"><rect x="1" y="3" width="14" height="10" fill="var(--red)"/><path d="M1 3 L8 9 L15 3" stroke="var(--white)" stroke-width="1.4" fill="none"/></svg>
    </p>
    <p class="contact__line">brindovalle
      <svg class="contact__icon" viewBox="0 0 16 16"><circle cx="8" cy="8" r="6.5" fill="none" stroke="var(--red)" stroke-width="1.6"/></svg>
    </p>
  </div>

  <p class="wordmark wordmark--front">Brindovalle</p>
</section>

<section class="card card--back" aria-label="Business card back">
  <div class="back-lockup">
    <span class="back-lockup__dot"></span>
    <p class="wordmark wordmark--back">Brindovalle</p>
  </div>
</section>

</body>
</html>
```